Brimsett Gardening Fresh New Website

We are looking to create a simple fresh website for our landscaping business. The website should appeal to a 'high end' audience. We deal with a lot of Embassies and affluent clients who have extremely large gardens that are meticulously maintained. The site is about communicating our excellent landscaping and customer service skills and encouraging new clients to reach out and engage us to take care of their gardens.

The website is basically going to be our business card, it will have almost no functionality other than two 'contact us' forms, one for smaller clients and one for more detailed projects.

The website will not have a lot of written content and will have to show photos of beautifully landscaped gardens.

The main logo in black will influence the site, however, we are open to all suggestions.

We are expecting to have the following pages:
Home Page
Services
About Us
Contact Us
Showcase (photo gallery of our work)

We need someone who can code it to wordpress and be available for minor changes over a number of days. They will be simple tweaks.

```html
<!DOCTYPE html>
<html lang="en">
<head>
<meta charset="utf-8">
<title>Brimsett Gardening</title>
<link href="https://fonts.googleapis.com/css2?family=Noto+Serif:wght@700&family=Roboto:wght@400;500;700&display=swap" rel="stylesheet">
<style>
:root{
  --brown:#a97b34;
  --brown-dark:#8f6526;
  --yellow:#fbd94f;
  --gold:#e4b52f;
  --navy:#1c2a4c;
  --ink:#1b1b1b;
  --text:#333;
  --white:#fff;
  --footer:#1c1c1c;
}
*{box-sizing:border-box;margin:0;padding:0}
html,body{width:1200px;height:3831px;overflow:hidden}
body{position:relative;background:var(--white);font-family:'Roboto',sans-serif;color:var(--text)}
.serif{font-family:'Noto Serif',serif;font-weight:700}
.btn{position:absolute;display:flex;align-items:center;justify-content:center;gap:8px;border-radius:30px;font:700 15px 'Roboto',sans-serif;text-transform:uppercase;white-space:nowrap}
.btn svg{width:14px;height:14px}
.btn-gold{background:linear-gradient(180deg,#f2c840,#d9a72a);color:var(--white)}
.btn-yellow{background:var(--yellow);color:var(--ink)}
.btn-outline{border:2px solid var(--white);color:var(--white)}
.btn-outline-dark{border:2px solid var(--ink);color:var(--ink)}

/* header */
.site-header{position:absolute;left:0;top:0;width:1200px;height:98px;background:var(--white);z-index:5}
.brand{position:absolute;left:111px;top:-30px;width:164px;height:180px;border-radius:50%;background:var(--white);display:flex;align-items:flex-end;justify-content:center;padding-bottom:48px;z-index:6}
.brand span{font:500 15px 'Roboto',sans-serif;color:var(--brown);letter-spacing:2px;text-transform:uppercase;text-align:center;line-height:1.4}
.nav{position:absolute;top:32px;left:369px;display:flex;font:500 15px 'Roboto',sans-serif;color:var(--ink)}
.nav a{color:var(--ink);text-decoration:none}
.nav .sep{margin:0 22px}
.login{left:960px;top:22px;width:127px;height:40px}

/* hero */
.hero{position:absolute;left:0;top:98px;width:1200px;height:680px;background:linear-gradient(160deg,#4d6b35 0%,#6f9a3d 30%,#5f8e34 55%,#a8a89a 75%,#6d9a3b 100%)}
.hero-shade{position:absolute;inset:0;background:linear-gradient(90deg,rgba(0,0,0,.35),rgba(0,0,0,0) 60%)}
.hero-curve{position:absolute;left:0;top:640px}
.hero h2{position:absolute;left:110px;top:190px;font-size:40px;color:var(--white);white-space:nowrap}
.hero h1{position:absolute;left:110px;top:258px;font-size:50px;line-height:1.2;color:var(--white);white-space:nowrap}
.hero p{position:absolute;left:110px;top:334px;width:580px;font:700 17px/27px 'Roboto',sans-serif;color:var(--white)}
.get-started{left:110px;top:404px;width:165px;height:42px}

.quote{position:absolute;left:745px;top:83px;width:343px;height:420px;background:var(--brown);z-index:6;padding:30px 34px}
.quote h3{font-size:22px;color:var(--white);text-align:center;margin-bottom:14px}
.field{background:var(--white);border-radius:18px;height:34px;margin-bottom:13px;padding:0 22px;font:12px/34px 'Roboto',sans-serif;color:#666}
.field.area{height:84px;line-height:30px}
.quote .btn{left:90px;top:392px;width:165px;height:44px}

/* services */
.section-title{position:absolute;left:0;width:1200px;text-align:center;font-size:38px}
.card{position:absolute;background:var(--brown);color:var(--white);text-align:center}
.card .icon{width:90px;height:90px;border-radius:50%;background:rgba(255,255,255,.75);margin:34px auto 22px}
.card h4{font:700 17px 'Roboto',sans-serif}
.card .btn{left:43px;width:140px;height:40px;font-size:14px}
.card.active{background:var(--yellow);color:var(--ink);border-bottom:4px solid var(--brown);box-shadow:0 6px 14px rgba(0,0,0,.15)}
.card.active .icon{background:none;border:2px solid var(--ink);width:70px;height:70px;margin:26px auto 16px}
.card.active p{font:13px/20px 'Roboto',sans-serif;color:#444;padding:0 10px;margin-top:12px;text-align:justify;text-align-last:center}

/* about */
.about-band{position:absolute;left:0;top:1334px;width:486px;height:516px;background:var(--brown)}
.about-photo{position:absolute;left:65px;top:1395px;width:512px;height:395px;background:var(--white);padding:7px}
.about-photo div{width:100%;height:100%;background:linear-gradient(135deg,#3f7d1d,#8ec63c 40%,#b8b2a4 70%,#5f6a55)}
.about h2{position:absolute;left:650px;top:1408px;font-size:38px;color:var(--ink)}
.about p{position:absolute;left:650px;top:1466px;width:437px;font:15px/26px 'Roboto',sans-serif;color:#333;text-align:justify}
.learn{left:650px;top:1722px;width:163px;height:42px}

/* gallery */
.gallery-band{position:absolute;left:0;top:1936px;width:1200px;height:344px;background:var(--yellow)}
.shot{position:absolute;width:310px;height:262px;border:2px solid var(--white);box-shadow:0 2px 6px rgba(0,0,0,.15)}

/* contact */
.contact{position:absolute;left:0;top:2816px;width:1200px;height:640px;background:linear-gradient(180deg,#b3873b,#a27330)}
.contact h2{color:var(--white)}
.input{position:absolute;background:var(--white);border-radius:22px;padding:0 22px;font:13px 'Roboto',sans-serif;color:#777;display:flex;align-items:center;justify-content:space-between}
.input.area{align-items:flex-start;padding-top:14px;border-radius:16px}
.contact .btn{left:517px;top:427px;width:166px;height:43px}

/* footer */
.footer-curve{position:absolute;left:0;top:3340px}
.footer{position:absolute;left:0;top:3460px;width:1200px;height:371px;background:var(--footer);color:var(--white)}
.footer-brand{position:absolute;left:111px;top:110px;font:500 22px/34px 'Roboto',sans-serif;letter-spacing:4px;color:var(--brown);text-transform:uppercase;text-align:center;width:200px}
.col{position:absolute;top:64px}
.col h5{font:500 16px 'Roboto',sans-serif;margin-bottom:20px;text-transform:uppercase}
.col li{list-style:none;display:flex;align-items:center;gap:12px;font:15px 'Roboto',sans-serif;height:36px}
.col li svg{width:14px;height:14px;flex:none}
.contact-item{display:flex;align-items:center;gap:14px;font:15px/22px 'Roboto',sans-serif;margin-bottom:22px}
.contact-item .dot{width:30px;height:30px;border-radius:50%;background:#2e2e2e;display:flex;align-items:center;justify-content:center;flex:none}
.contact-item svg{width:14px;height:14px}
.footer hr{position:absolute;left:111px;top:294px;width:977px;border:0;border-top:1px solid #555}
.copy{position:absolute;left:0;top:320px;width:1200px;text-align:center;font:13px 'Roboto',sans-serif}
</style>
</head>
<body>
<svg width="0" height="0" style="position:absolute">
  <defs>
    <symbol id="arrow-circle" viewBox="0 0 16 16"><circle cx="8" cy="8" r="8" fill="currentColor"/><path d="M5 8h5M8 5l3 3-3 3" stroke="var(--btnbg,#d9a72a)" stroke-width="2" fill="none"/></symbol>
    <symbol id="arrow-yellow" viewBox="0 0 16 16"><circle cx="8" cy="8" r="8" fill="#fbd94f"/><path d="M4.5 8h5.5M8 5l3 3-3 3" stroke="#1c1c1c" stroke-width="2" fill="none"/></symbol>
  </defs>
</svg>

<header class="site-header">
  <div class="brand"><span>Brimsett<br>Gardening</span></div>
  <nav class="nav">
    <a>HOME</a><span class="sep">|</span><a>ABOUT US</a><span class="sep">|</span><a>SERVICES</a><span class="sep">|</span><a>GALLERY</a><span class="sep">|</span><a>CONTACT US</a>
  </nav>
  <a class="btn btn-gold login">Login
    <svg viewBox="0 0 16 16"><circle cx="8" cy="5" r="3.2" fill="#fff"/><path d="M2 15c0-4 2.7-6 6-6s6 2 6 6z" fill="#fff"/></svg>
  </a>
</header>

<section class="hero" role="img" aria-label="Landscaped lawn with a curving brick path and stepping stones">
  <div class="hero-shade"></div>
  <h2 class="serif">WELCOME TO</h2>
  <h1 class="serif">BRIMSETT GARDENING</h1>
  <p>Lorem ipsum dolor sit amet, consectetur adipiscing elit, sed do eiusmod tempor incididunt ut labore et dolore magna aliquat enim ad minimed.</p>
  <a class="btn btn-gold get-started">Get Started <svg style="color:#fff"><use href="#arrow-circle"/></svg></a>
  <svg class="hero-curve" width="1200" height="140" viewBox="0 0 1200 140">
    <path d="M0,40 Q600,170 1200,30 L1200,140 L0,140Z" fill="#fbd94f"/>
    <path d="M0,55 Q600,230 1200,38 L1200,140 L0,140Z" fill="#fff"/>
  </svg>
</section>

<form class="quote">
  <h3 class="serif">GET FREE QUOTES</h3>
  <div class="field">Enter Name</div>
  <div class="field">Enter Email</div>
  <div class="field">Enter Phone</div>
  <div class="field">Enter Address</div>
  <div class="field area">Message</div>
  <a class="btn btn-yellow">Submit Now <svg style="color:#1b1b1b;--btnbg:#fbd94f"><use href="#arrow-circle"/></svg></a>
</form>

<h2 class="section-title serif" style="top:848px;color:var(--ink)">OUR SERVICES</h2>

<div class="card" style="left:111px;top:956px;width:225px;height:272px">
  <div class="icon" role="img" aria-label="Tree planting icon"></div>
  <h4>Lorem ipsum dolor sit</h4>
  <a class="btn btn-outline" style="top:196px">Read More <svg style="color:#fff;--btnbg:#a97b34"><use href="#arrow-circle"/></svg></a>
</div>
<div class="card active" style="left:361px;top:934px;width:226px;height:312px">
  <div class="icon" role="img" aria-label="Landscape design icon"></div>
  <h4>Lorem ipsum dolor sit</h4>
  <p>Lorem ipsum dolor consectetur adipiscing sed eiusmode tempor incididuntt dolore magna aliqua. enim minim veniam quis</p>
  <a class="btn btn-outline-dark" style="top:242px">Read More <svg style="color:#1b1b1b;--btnbg:#fbd94f"><use href="#arrow-circle"/></svg></a>
</div>
<div class="card" style="left:613px;top:956px;width:224px;height:272px">
  <div class="icon" role="img" aria-label="Farmland icon"></div>
  <h4>Lorem ipsum dolor sit</h4>
  <a class="btn btn-outline" style="top:196px">Read More <svg style="color:#fff;--btnbg:#a97b34"><use href="#arrow-circle"/></svg></a>
</div>
<div class="card" style="left:862px;top:956px;width:226px;height:272px">
  <div class="icon" role="img" aria-label="Seedling icon"></div>
  <h4>Lorem ipsum dolor sit</h4>
  <a class="btn btn-outline" style="top:196px">Read More <svg style="color:#fff;--btnbg:#a97b34"><use href="#arrow-circle"/></svg></a>
</div>

<section class="about">
  <div class="about-band"></div>
  <div class="about-photo"><div role="img" aria-label="Stepping stone path through gravel lined with bamboo"></div></div>
  <h2 class="serif">ABOUT US</h2>
  <p>Lorem ipsum dolor sit amet, consectetur adipiscing elit, sed do eiusmod tempor incididunt ut labore et dolore magna aliqua. Ut enim ad minim veniam, quis nostrud exercitation ullamco laboris nisi ut aliquip ex ea commodo consequat. Duis aute irure dolor in reprehenderit in voluptate velit esse cillum dolore eu fugiat nulla pariatur. Excepteur sint occaecat cupidatat non proident, sunt in culpa qui officia deserunt mollit anim id est laborum.Perspiciatis unde omnis iste natus error sit voluptatem accusantium doloremque laudantium totam rem aperiam eaqued.</p>
  <a class="btn btn-gold learn">Learn More <svg style="color:#fff"><use href="#arrow-circle"/></svg></a>
</section>

<section class="gallery">
  <div class="gallery-band"></div>
  <h2 class="section-title serif" style="top:2022px;color:var(--navy)">OUR GALLERY</h2>
  <div class="shot" style="left:110px;top:2168px;background:linear-gradient(160deg,#3b5a2a,#7cae3c 55%,#c8c4b4 75%,#6aa13a)" role="img" aria-label="Curving stone path across a lawn"></div>
  <div class="shot" style="left:443px;top:2168px;background:linear-gradient(160deg,#456b2c,#8aa94b 40%,#b5b2ac 65%,#8a6a44)" role="img" aria-label="Rock garden with timber steps"></div>
  <div class="shot" style="left:778px;top:2168px;background:linear-gradient(180deg,#9fb8d6,#5f8a3d 40%,#a7a39d 75%,#8b877f)" role="img" aria-label="Paved patio with outdoor dining set"></div>
  <div class="shot" style="left:110px;top:2466px;background:linear-gradient(170deg,#e8ecef,#6f7b6b 45%,#7aa945 75%,#d6d6d2)" role="img" aria-label="Modern house with landscaped front garden"></div>
  <div class="shot" style="left:443px;top:2466px;background:linear-gradient(170deg,#4d7a2c,#2f4a24 40%,#8f8a7e 75%,#54703a)" role="img" aria-label="Bamboo garden with cobbled path"></div>
  <div class="shot" style="left:778px;top:2466px;background:linear-gradient(160deg,#3f6a2a,#6c9b3a 45%,#9a968c 70%,#5a8a35)" role="img" aria-label="Topiary garden with winding cobble path"></div>
</section>

<section class="contact">
  <h2 class="section-title serif" style="top:60px">GET IN TOUCH</h2>
  <div class="input" style="left:162px;top:130px;width:431px;height:38px">Enter Name</div>
  <div class="input" style="left:607px;top:130px;width:431px;height:38px">Enter Email</div>
  <div class="input" style="left:162px;top:186px;width:286px;height:41px">Phone</div>
  <div class="input" style="left:458px;top:186px;width:284px;height:41px">Date</div>
  <div class="input" style="left:752px;top:186px;width:286px;height:41px">Services <span>⌄</span></div>
  <div class="input" style="left:162px;top:244px;width:431px;height:42px">Enter Address</div>
  <div class="input" style="left:607px;top:244px;width:431px;height:42px">Prices <span>⌄</span></div>
  <div class="input area" style="left:162px;top:302px;width:876px;height:95px">Message</div>
  <a class="btn btn-yellow">Submit Now <svg style="color:#1b1b1b;--btnbg:#fbd94f"><use href="#arrow-circle"/></svg></a>
</section>

<svg class="footer-curve" width="1200" height="130" viewBox="0 0 1200 130">
  <path d="M0,110 Q600,-50 1200,110 L1200,130 L0,130Z" fill="#fbd94f"/>
  <path d="M0,125 Q600,-10 1200,125 L1200,130 L0,130Z" fill="#1c1c1c"/>
</svg>

<footer class="footer">
  <div class="footer-brand">Brimsett<br>Gardening</div>
  <div class="col" style="left:390px">
    <h5>Quick Links</h5>
    <ul>
      <li><svg><use href="#arrow-yellow"/></svg>Home</li>
      <li><svg><use href="#arrow-yellow"/></svg>About Us</li>
      <li><svg><use href="#arrow-yellow"/></svg>Services</li>
      <li><svg><use href="#arrow-yellow"/></svg>Gallery</li>
      <li><svg><use href="#arrow-yellow"/></svg>Contact Us</li>
    </ul>
  </div>
  <div class="col" style="left:601px">
    <h5>Other&nbsp; Links</h5>
    <ul>
      <li><svg><use href="#arrow-yellow"/></svg>FAQs</li>
      <li><svg><use href="#arrow-yellow"/></svg>Terms &amp; Conditions</li>
      <li><svg><use href="#arrow-yellow"/></svg>Support</li>
      <li><svg><use href="#arrow-yellow"/></svg>Sitemap</li>
      <li><svg><use href="#arrow-yellow"/></svg>Privacy Policy</li>
    </ul>
  </div>
  <div class="col" style="left:873px">
    <h5>Contact Us</h5>
    <div class="contact-item"><span class="dot"><svg viewBox="0 0 16 16"><path d="M3 1l3 1 1 3-2 1.5a9 9 0 0 0 4.5 4.5L11 9l3 1 1 3-2 2C7 15 1 9 1 3z" fill="#fbd94f"/></svg></span>+1 888 888 8888</div>
    <div class="contact-item"><span class="dot"><svg viewBox="0 0 16 16"><rect x="1" y="3" width="14" height="10" fill="#fbd94f"/><path d="M1 3l7 6 7-6" stroke="#2e2e2e" stroke-width="1.5" fill="none"/></svg></span>info@brimsettgardening.com</div>
    <div class="contact-item"><span class="dot"><svg viewBox="0 0 16 16"><path d="M8 1a5 5 0 0 1 5 5c0 4-5 9-5 9S3 10 3 6a5 5 0 0 1 5-5z" fill="#fbd94f"/><circle cx="8" cy="6" r="2" fill="#2e2e2e"/></svg></span><span>1288,Lorem ipsum dolor<br>&nbsp;consectetur adipiscing</span></div>
  </div>
  <hr>
  <p class="copy">Copyrights © Brimsett Gardening 2024 | Allrights Reserved</p>
</footer>
</body>
</html>
```